Systems and Technology Consultants - Website

Design & Build a website for a new company which operates in the Systems and Technology space for Transportation, Government and Commercial sectors.

Overall design should be minimalist in nature.
Should also have a feed that provides news and event updates on the main page.
Logo has already been awarded and should be incorporated into the site.

We like the overall layout, functionality and simplicity of the below sites. Submitted designs could be similar to or a combination of the aspects on these sites, or perhaps a whole different concept - we are open to new ideas.
Norvique.com
Teblo.it

Update 1 Dated 27 May 2014

All I am moving away from the Teblo.it website and would like it to be more aligned with Norvique.com not only in layout but in functionality. I will be extending the deadline of this design brief for two weeks to incorporate additional requirements and will add addtional funding to the project.

Apologies for not having more information available to provide but with so many submissions its getting confusing.

Thanks Derek

Please note that the brief has been updated and the deadline has been extended.

Important: We will need two language versions of the website, English and Arabic; the website is hosted on HostPelican

Hello All, Thank you for your submissions. We have narrowed it down to the final 6 designers and I just wanted to take a moment and provide a bit of feedback regarding the concepts that we like and the modifications we are looking for. First, let me mention some of the design functions we like. - At the top of the homepage we really like the "region" or "language" tab so that the website can be viewed in both English and Arabic. - We like the homepage to have clear color variation so that the different sections of the homepage are distinct. Additionally, we like the bottom portion of the homepage to be in red. We feel that draws attention to our contact information. Again, we would like the colors to integrate black, gray-scale, red, etc. - Having a search tab at the top of the home page, or integrated into the main image, so that the site is easy to navigate. - We especially like the main image to have the scrolling tabs at the bottom so it is easy to browse the services offered (Consultancy, Solutions Architecture, Masters Systems Integration, Independent Design Review). - In regards to the services offered tab we really like the idea that a few people presented that have the outside of our logo with an icon in the middle of consultancy, solutions, etc., etc. Secondly, as mentioned in our brief we really enjoy the design of norvique site. Specially, we enjoy the strong iconic images they use, the way the tabs at the top scroll easily, and contact us page that generates an email. Lastly, I've included some photos of the concept we have been working on. What we are trying to demonstrate is how our company offers a range of services that are essentially linked together. We provide individual services that when combined present the full service package. We would like this concept to be integrated into the over concept of our website. Please feel free to ask for clarification of any of the above points or contact us if you have any additional questions. We appreciate all of your hard work and are very excited to see the updated designs. Best, Marta Vennick Quelbrant Senior Program Manager marta.vennick@quelbrant-example.com

Industry/Entity Type

Government

Font styles to use
Serif
Sans Serif

Requirements
Must have
• Must work on/adapt to various/mobile devices (responsive)
Must be simple and straightforward
Colors should be in line/matching with logo
2 language versions: English and Arabic (no Thai)
Services should be the first group/row of items after/below the main image
Note: the website will be hosted by hostpelican
Nice to have
• Submit feedback form
What's New section
The banner at the bottom of the site should not be too large; we would like a narrow one more
It would be nice if the header/top banner (with Home, About, etc. tabs) could stay in place as you scroll down (like Norvique and Chatterloop)
We will likely only use one image with a Company slogan on the Home page rather than a carousel of images to rotate through
Should not have
• This is the existing website: http://www.quelbrant-example.org
We do not like the animation, the way the banner icons/titles bounce
Not simple enough, we don't like the functionality or how pages load so slowly
We do not like the logo centered - it should be at the left
The banner and its tabs should not be towards the right, we would like them to be centered, to go all the way across and to be below the logo

```html
<!DOCTYPE html>
<html lang="en">
<head>
<meta charset="utf-8">
<title>Quelbrant — Systems and Technology Consultants</title>
<link href="https://fonts.googleapis.com/css2?family=Open+Sans:ital,wght@0,400;0,600;0,700;1,600;1,700&display=swap" rel="stylesheet">
<style>
:root{
  --red:#d71f2b;
  --red-dark:#b3141f;
  --ink:#2b2b2b;
  --muted:#6d6d6d;
  --light:#9a9a9a;
  --nav:#e9e9e9;
  --tint:#fbeff1;
  --line:#e2d5d8;
  --footer:#2a2a2a;
  --footer-bar:#1c1c1c;
  --green:#6cb33f;
  --orange:#f29a1f;
  --white:#ffffff;
}
*{box-sizing:border-box;margin:0;padding:0}
html,body{width:750px;height:1200px;overflow:hidden}
body{font-family:"Open Sans",Arial,sans-serif;color:var(--ink);background:var(--white);font-size:8px;line-height:1.45}
.wrap{width:550px;margin:0 auto;position:relative}

/* header */
.site-header{height:88px;background:var(--white)}
.brand-row{height:60px;display:flex;align-items:center;justify-content:space-between}
.brand{display:flex;align-items:center;gap:6px;font-weight:700;font-size:15px;color:var(--red);letter-spacing:1px}
.brand-mark{width:14px;height:14px;background:var(--red)}
.search{display:flex;align-items:center;gap:4px}
.search-field{width:92px;height:16px;border:1px solid #d4d4d4;font-size:7px;color:var(--light);padding:2px 5px}
.lang{height:16px;padding:0 6px;background:#5a86b8;color:var(--white);font-size:7px;line-height:16px}
.main-nav{height:26px;background:var(--nav);display:flex;border-top:1px solid #dcdcdc;border-bottom:1px solid #d0d0d0}
.main-nav a{flex:1;text-align:center;line-height:25px;font-size:7px;font-weight:600;color:#555;text-decoration:none;text-transform:uppercase}
.main-nav a.active{background:var(--red);color:var(--white)}

/* hero */
.hero{height:322px;position:relative;background:linear-gradient(120deg,#0c3a6e 0%,#1d5f9e 40%,#6aa0cf 62%,#c9d6e3 78%,#8a96a6 100%)}
.hero-caption{position:absolute;left:112px;top:190px;width:300px;height:90px;background:rgba(255,255,255,.9);padding:12px 14px}
.hero-caption h2{font-size:14px;font-style:italic;font-weight:700;color:var(--ink);margin-bottom:5px}
.hero-caption p{font-size:7px;color:var(--muted);margin-bottom:7px}
.btn{display:inline-block;background:var(--red);color:var(--white);font-size:6.5px;font-weight:700;padding:3px 8px;text-transform:uppercase}

/* welcome */
.welcome{height:310px;background:var(--tint);padding-top:40px}
.welcome .wrap{display:flex;gap:28px}
.welcome-text{width:262px}
.section-title{font-size:12px;font-weight:700;color:var(--ink);margin-bottom:10px}
.welcome-text p{font-size:7px;color:var(--muted);margin-bottom:8px}
.services{width:260px;display:grid;grid-template-columns:repeat(3,1fr);gap:6px;margin-top:4px}
.service{background:var(--white);border:1px solid var(--line);height:100px;text-align:center;padding:10px 5px}
.service-icon{width:22px;height:22px;border-radius:50%;margin:0 auto 6px;display:flex;align-items:center;justify-content:center}
.service-icon.green{background:var(--green)}
.service-icon.red{background:var(--red)}
.service-icon.orange{background:var(--orange)}
.service h3{font-size:7px;font-weight:700;color:var(--red);margin-bottom:3px}
.service p{font-size:5.5px;color:var(--light);line-height:1.4}

/* news */
.news{height:240px;padding-top:22px}
.news-head{display:flex;justify-content:space-between;align-items:center}
.arrows{display:flex;gap:3px}
.arrows span{width:12px;height:12px;background:#cfcfcf;display:flex;align-items:center;justify-content:center}
.news-grid{display:grid;grid-template-columns:repeat(4,1fr);gap:12px}
.news-card{border:1px solid #e3e3e3;height:168px}
.news-img{height:80px}
.news-img.a{background:linear-gradient(135deg,#0f2f55,#3f7cb8)}
.news-img.b{background:linear-gradient(135deg,#1b1b1b,#5a5a5a)}
.news-img.c{background:linear-gradient(135deg,#14395f,#7fb2de)}
.news-img.d{background:linear-gradient(135deg,#dfe7ee,#6b8fb1)}
.news-body{padding:6px 7px}
.news-body h4{font-size:7px;font-weight:600;color:var(--ink);margin-bottom:4px}
.news-body .date{font-size:6px;color:var(--light)}
.news-body .more{display:block;text-align:right;font-size:6.5px;font-weight:700;color:var(--red);margin-top:14px}

/* clients */
.clients{height:90px;padding-top:8px}
.client-row{display:flex;justify-content:space-between;align-items:center;margin-top:2px;padding:0 6px}
.client{display:flex;align-items:center;gap:4px;font-size:9px;font-weight:600;color:#8a8a8a;text-transform:uppercase}
.client i{width:10px;height:10px;border-radius:50%;background:#b5b5b5;display:block}

/* tweets */
.tweets{height:75px;padding-top:2px}
.tweet-row{display:flex;gap:30px}
.tweet{display:flex;gap:6px;width:260px}
.tweet-icon{width:12px;height:12px;border-radius:50%;background:var(--red);flex:none;margin-top:1px}
.tweet p{font-size:6.5px;color:var(--muted)}
.tweet .time{color:var(--red);font-size:6px}

/* footer */
.site-footer{height:57px;background:var(--footer);color:#bdbdbd;padding-top:7px}
.footer-cols{display:grid;grid-template-columns:repeat(4,1fr);gap:14px}
.footer-cols h5{font-size:7px;color:var(--white);font-weight:700;margin-bottom:2px}
.footer-cols li{list-style:none;font-size:5.5px;line-height:1.5;display:flex;align-items:center;gap:3px}
.footer-cols li i{width:5px;height:5px;background:var(--red);display:block}
.footer-bar{height:18px;background:var(--footer-bar);color:#8c8c8c;font-size:5.5px}
.footer-bar .wrap{display:flex;justify-content:space-between;line-height:18px}
</style>
</head>
<body>

<header class="site-header">
  <div class="wrap brand-row">
    <div class="brand"><span class="brand-mark"></span>QUELBRANT</div>
    <div class="search">
      <div class="search-field">Search</div>
      <div class="lang">عربي</div>
    </div>
  </div>
  <nav class="wrap main-nav">
    <a class="active">Home</a>
    <a>Business Units</a>
    <a>Services</a>
    <a>About Us</a>
    <a>Locations</a>
    <a>Contact Us</a>
  </nav>
</header>

<section class="hero" role="img" aria-label="Photo of a business hand touching a glowing blue digital interface with a world map">
  <div class="hero-caption">
    <h2>Systems Professionals</h2>
    <p>We deliver consulting, design and integration services for transport, government and commercial clients across the region.</p>
    <span class="btn">Read More</span>
  </div>
</section>

<section class="welcome">
  <div class="wrap">
    <div class="welcome-text">
      <h2 class="section-title">Welcome To Quelbrant</h2>
      <p>Quelbrant specializes in delivering quality professional services and technical projects that support large transport goals, systems and tools that improve how people move and work. We combine field knowledge with modern engineering to create reliable, lasting results.</p>
      <p>Our team brings together consultants, architects and integrators who work closely with each client from planning to handover, keeping every system simple, secure and ready for growth.</p>
      <span class="btn">Read More</span>
    </div>
    <div class="services">
      <div class="service"><div class="service-icon green"><svg width="10" height="10" viewBox="0 0 10 10"><path d="M2 5l2 2 4-4" stroke="#fff" stroke-width="1.6" fill="none"/></svg></div><h3>Consulting</h3><p>Clear advice for planning complex systems.</p></div>
      <div class="service"><div class="service-icon red"><svg width="10" height="10" viewBox="0 0 10 10"><circle cx="5" cy="5" r="3" stroke="#fff" stroke-width="1.4" fill="none"/></svg></div><h3>Engineering</h3><p>Solution design built for long service.</p></div>
      <div class="service"><div class="service-icon orange"><svg width="10" height="10" viewBox="0 0 10 10"><rect x="2" y="2" width="6" height="6" stroke="#fff" stroke-width="1.4" fill="none"/></svg></div><h3>Construction</h3><p>Site delivery managed on time and budget.</p></div>
      <div class="service"><div class="service-icon red"><svg width="10" height="10" viewBox="0 0 10 10"><path d="M2 8V4M5 8V2M8 8V5" stroke="#fff" stroke-width="1.5"/></svg></div><h3>Operations</h3><p>Daily running of live networks.</p></div>
      <div class="service"><div class="service-icon red"><svg width="10" height="10" viewBox="0 0 10 10"><path d="M2 5h6M5 2v6" stroke="#fff" stroke-width="1.6"/></svg></div><h3>Maintenance</h3><p>Care plans that keep assets working.</p></div>
      <div class="service"><div class="service-icon orange"><svg width="10" height="10" viewBox="0 0 10 10"><path d="M5 1l1.2 2.6L9 4 7 6l.5 3L5 7.6 2.5 9 3 6 1 4l2.8-.4z" fill="#fff"/></svg></div><h3>Support</h3><p>Help desk ready around the clock.</p></div>
    </div>
  </div>
</section>

<section class="news">
  <div class="wrap">
    <div class="news-head">
      <h2 class="section-title">News &amp; Events</h2>
      <div class="arrows">
        <span><svg width="6" height="6" viewBox="0 0 6 6"><path d="M4 1L2 3l2 2" stroke="#fff" fill="none"/></svg></span>
        <span><svg width="6" height="6" viewBox="0 0 6 6"><path d="M2 1l2 2-2 2" stroke="#fff" fill="none"/></svg></span>
      </div>
    </div>
    <div class="news-grid">
      <article class="news-card"><div class="news-img a" role="img" aria-label="Photo of blue data network lights"></div><div class="news-body"><h4>New transit control center opens this spring</h4><span class="date">20 minutes ago</span><span class="more">Read More »</span></div></article>
      <article class="news-card"><div class="news-img b" role="img" aria-label="Photo of a server room"></div><div class="news-body"><h4>Team joins regional systems summit in May</h4><span class="date">20 minutes ago</span><span class="more">Read More »</span></div></article>
      <article class="news-card"><div class="news-img c" role="img" aria-label="Photo of a digital circuit board"></div><div class="news-body"><h4>Design review completed for city rail line</h4><span class="date">20 minutes ago</span><span class="more">Read More »</span></div></article>
      <article class="news-card"><div class="news-img d" role="img" aria-label="Photo of engineers reviewing plans"></div><div class="news-body"><h4>We welcome three senior integration leads</h4><span class="date">20 minutes ago</span><span class="more">Read More »</span></div></article>
    </div>
  </div>
</section>

<section class="clients">
  <div class="wrap">
    <h2 class="section-title">Our Clients</h2>
    <div class="client-row">
      <span class="client"><i></i>Business</span>
      <span class="client"><i></i>Your Logo</span>
      <span class="client"><i></i>Business</span>
      <span class="client">Brand</span>
      <span class="client">Designer</span>
      <span class="client"><i></i>Logo</span>
    </div>
  </div>
</section>

<section class="tweets">
  <div class="wrap">
    <h2 class="section-title">Latest Tweet</h2>
    <div class="tweet-row">
      <div class="tweet"><span class="tweet-icon"></span><p>Our new service guide is now online, read how we link each service into one package. <span class="time">20 minutes ago</span></p></div>
      <div class="tweet"><span class="tweet-icon"></span><p>Meet our team at the regional transport expo next week, stand twelve in hall two. <span class="time">20 minutes ago</span></p></div>
    </div>
  </div>
</section>

<footer class="site-footer">
  <div class="wrap footer-cols">
    <div><h5>Quick Links</h5><ul><li>Home</li><li>About Us</li><li>Services</li></ul></div>
    <div><h5>Help &amp; Support</h5><ul><li>FAQ</li><li>Live Support</li><li>Send Mail</li></ul></div>
    <div><h5>Social Connection</h5><ul><li><i></i>Chatterloop</li><li><i></i>Chirpwell</li><li><i></i>Plusora</li></ul></div>
    <div><h5>Get in touch</h5><ul><li>+000 01 555 0184</li><li>info@quelbrant-example.org</li><li>Harbor Road, Meridan City</li></ul></div>
  </div>
</footer>
<div class="footer-bar">
  <div class="wrap"><span>Sitemap | Privacy Policy</span><span>Copyright 2014 Quelbrant. All rights reserved.</span></div>
</div>

</body>
</html>
```